Business Card Design

Buy and sell properties
Buy and rehab properties
Buy properties for cash
That is what I do but do need a logo
looking for some type of logo or design on it
Just started business
Back of card should say something like BUY HOUSES CASH
Overview: it is a new company. Basically I buy properties wholesale and fix them up and sell them or sell them to other fix and flippers
Background: company is new so not any background
Market: is basically anyone selling a house or buying a house. Someone that needs to sell house fast. Basically I am a cash home buyer!!!

Updates
Email on card should be:   harborlanerealtyinc@mailnest.com

Industry/Entity Type
House
Contact Information for Business Card
Harbor Lane Realty Inc
PO Box 718296
Coral Mill Key FL 33071

Dwight Kallum
dkallum@mailnest.com
305-271-5589

```html
<!DOCTYPE html>
<html lang="en">
<head>
<meta charset="utf-8">
<title>Harbor Lane Realty Inc – Business Card</title>
<link rel="stylesheet" href="https://fonts.googleapis.com/css2?family=Exo+2:wght@300;400;700&display=swap">
<style>
  :root {
    --navy: #262a6e;
    --navy-deep: #1d205a;
    --card-white: #f7f7f9;
    --text-soft: #3a3d72;
    --page: #e9e7e3;
    --shadow: rgba(20, 22, 50, 0.18);
  }
  * { box-sizing: border-box; margin: 0; padding: 0; }
  html, body {
    width: 1200px; height: 885px; overflow: hidden;
    background: var(--page);
    font-family: "Exo 2", sans-serif;
  }
  .canvas {
    position: relative; width: 1200px; height: 885px;
  }
  .card {
    position: absolute; left: 300px; width: 600px; height: 343px;
    border-radius: 16px; overflow: hidden;
    background: var(--card-white);
    box-shadow: 0 10px 28px var(--shadow);
  }
  .card--front { top: 62px; }
  .card--back { top: 480px; }

  .front-band { position: absolute; inset: 0; width: 600px; height: 343px; }

  .brand {
    position: absolute; display: flex; align-items: center; gap: 12px;
    font-weight: 300; letter-spacing: 0.5px;
  }
  .brand-mark { width: 14px; height: 14px; }
  .card--front .brand {
    left: 300px; top: 58px; color: #ffffff; font-size: 25px;
  }
  .card--front .brand-mark { background: #ffffff; }

  .holder-name {
    position: absolute; left: 42px; top: 182px;
    font-size: 33px; font-weight: 400; color: var(--navy);
  }
  .contact-list {
    position: absolute; left: 44px; top: 236px; list-style: none;
    color: var(--text-soft); font-size: 15px; font-weight: 300; line-height: 22px;
  }
  .contact-list li { display: flex; align-items: flex-start; gap: 10px; }
  .contact-list svg { width: 13px; height: 13px; margin-top: 4px; flex: none; fill: var(--navy); }

  .card--back .brand {
    left: 0; right: 0; top: 118px; justify-content: center;
    color: var(--navy); font-size: 32px;
  }
  .card--back .brand-mark { background: var(--navy); width: 18px; height: 18px; }
  .tagline {
    position: absolute; left: 0; right: 0; top: 186px; text-align: center;
    color: var(--navy); font-size: 24px; font-weight: 700; letter-spacing: 0.5px;
  }
</style>
</head>
<body>
<main class="canvas">

  <section class="card card--front" aria-label="Card front">
    <svg class="front-band" viewBox="0 0 600 343" aria-hidden="true">
      <defs>
        <linearGradient id="bandShade" x1="0" y1="0" x2="1" y2="1">
          <stop offset="0" stop-color="#2e3380"/>
          <stop offset="1" stop-color="#1d205a"/>
        </linearGradient>
      </defs>
      <path d="M0 0 H600 V118 Q330 215 0 128 Z" fill="url(#bandShade)"/>
      <path d="M0 140 Q330 228 600 128" fill="none" stroke="var(--navy)" stroke-width="2"/>
    </svg>

    <div class="brand"><span class="brand-mark"></span>Harbor Lane Realty Inc</div>

    <h1 class="holder-name">Dwight Kallum</h1>
    <ul class="contact-list">
      <li>
        <svg viewBox="0 0 16 16"><path d="M3 1l3 3-1.5 2a9 9 0 005 5L11.5 9.5l3 3-2 2.5C7 15 1 9 1 3z"/></svg>
        305-271-5589
      </li>
      <li>
        <svg viewBox="0 0 16 16"><path d="M1 3h14v10H1z M1 3l7 6 7-6" fill="none" stroke="var(--navy)" stroke-width="1.6"/></svg>
        dkallum@mailnest.com
      </li>
      <li>
        <svg viewBox="0 0 16 16"><path d="M8 1l7 6h-2v8h-4v-5H7v5H3V7H1z"/></svg>
        PO Box 718296 Coral Mill Key<br>FL 33071
      </li>
    </ul>
  </section>

  <section class="card card--back" aria-label="Card back">
    <div class="brand"><span class="brand-mark"></span>Harbor Lane Realty Inc</div>
    <p class="tagline">BUY HOUSES CASH</p>
  </section>

</main>
</body>
</html>
```